Box truck wrap design for my business BrightNest Seal and Footing

A simple, modern design for a box truck. Truck dimensions are as follows.

Sides - 181"W x 84"H
Back Rollup Door - 87 3/4"W x 85 1/4"H

Brand guidelines have been attached along with examples of wraps that I like. Just need to apply this to an varnok box truck. Website is brightnest-crew.example which you can use as inspiration. Slogan is 'Snug Walls, Steady Halls"

Target Market(s)

Insulation, Waterproofing, Foundation Repair

Industry/Entity Type

Construction - Home Services

Font styles to use
Other font styles liked:
• use brand guidelines attached

Colors

Designer to choose colors to be used in the design.

Requirements
Must have
• brightnest-crew.example , 555-271-6384

```html
<!DOCTYPE html>
<html lang="en">
<head>
<meta charset="utf-8">
<title>BrightNest Seal and Footing – Box Truck Wrap Panels</title>
<link rel="stylesheet" href="https://fonts.googleapis.com/css2?family=Audiowide&family=Exo+2:ital,wght@1,800&family=Michroma&family=Poppins:wght@500;600&display=swap">
<style>
  :root {
    --canvas: #eceef0;
    --orange: #e8390e;
    --orange-deep: #d42a0a;
    --orange-bright: #f35a1c;
    --black: #0d0d0d;
    --charcoal: #1c1c1c;
    --grey: #8a8d91;
    --grey-dark: #55585c;
    --band: #efefef;
    --white: #ffffff;
  }
  * { box-sizing: border-box; margin: 0; padding: 0; }
  html, body { width: 1200px; height: 2282px; overflow: hidden; }
  body { background: var(--canvas); position: relative; font-family: "Poppins", sans-serif; }

  .panel { position: absolute; overflow: hidden; box-shadow: 0 6px 18px rgba(0,0,0,.12); }
  .panel-art { position: absolute; inset: 0; width: 100%; height: 100%; }

  /* side panels */
  .side { width: 1040px; height: 480px; left: 80px; }
  .side--street { top: 120px; }
  .side--curb { top: 920px; }
  .side--curb .panel-art { transform: scaleX(-1); }

  .side-copy { position: absolute; top: 0; width: 740px; height: 480px; text-align: center; }
  .side--street .side-copy { left: 290px; }
  .side--curb .side-copy { left: 20px; }

  .services { color: var(--white); font-weight: 600; font-size: 18px; letter-spacing: .2px; position: absolute; left: 0; right: 0; }
  .brand-name { font-family: "Audiowide", sans-serif; color: var(--black); line-height: 1; position: absolute; left: 0; right: 0; }
  .brand-sub { font-family: "Michroma", sans-serif; color: var(--white); background: var(--grey); position: absolute; left: 50%; transform: translateX(-50%); white-space: nowrap; line-height: 1; }
  .slogan { font-family: "Exo 2", sans-serif; font-style: italic; font-weight: 800; color: var(--orange); position: absolute; left: 0; right: 0; text-transform: uppercase; }
  .phone { color: var(--white); font-weight: 600; position: absolute; left: 0; right: 0; display: flex; justify-content: center; align-items: center; gap: 8px; }
  .phone svg { display: block; }
  .web-pill { font-family: "Michroma", sans-serif; color: var(--white); background: var(--black); border-radius: 20px; position: absolute; left: 50%; transform: translateX(-50%); white-space: nowrap; line-height: 1; }

  .side .services { top: 86px; }
  .side .brand-name { top: 158px; font-size: 66px; }
  .side .brand-sub { top: 234px; font-size: 22px; letter-spacing: 9px; padding: 5px 14px 5px 23px; }
  .side .slogan { top: 272px; font-size: 25px; letter-spacing: 3px; }
  .side .phone { top: 355px; font-size: 32px; }
  .side .web-pill { top: 410px; font-size: 17px; padding: 9px 20px; }

  /* rear doors */
  .rear { width: 440px; height: 430px; top: 1670px; }
  .rear--orange { left: 90px; }
  .rear--black { left: 670px; }
  .rear .brand-name { top: 180px; font-size: 46px; text-align: center; }
  .rear .brand-sub { top: 233px; font-size: 15px; letter-spacing: 6px; padding: 4px 10px 4px 16px; }
  .rear .slogan { top: 259px; font-size: 17px; letter-spacing: 2px; text-align: center; }
  .rear .services { top: 318px; font-size: 13px; text-align: center; }
  .rear .phone { top: 340px; font-size: 24px; }
  .rear .web-pill { top: 380px; font-size: 13px; padding: 6px 14px; }
  .rear--black .services { color: var(--orange-bright); }
  .rear--black .web-pill { background: var(--orange); }
</style>
</head>
<body>

<!-- Street-side panel -->
<section class="panel side side--street">
  <svg class="panel-art" viewBox="0 0 1040 480" preserveAspectRatio="none" aria-hidden="true">
    <defs>
      <linearGradient id="sideOrange" x1="0" y1="0" x2="1" y2="1">
        <stop offset="0" stop-color="#f04a14"/><stop offset=".6" stop-color="#e8390e"/><stop offset="1" stop-color="#d42a0a"/>
      </linearGradient>
    </defs>
    <rect width="1040" height="480" fill="url(#sideOrange)"/>
    <polygon points="0,0 300,0 250,140 250,340 300,480 0,480" fill="#0d0d0d"/>
    <polygon points="300,0 325,0 275,140 250,140" fill="#ffffff"/>
    <polygon points="250,340 275,340 325,480 300,480" fill="#ffffff"/>
    <rect x="250" y="140" width="790" height="196" fill="#efefef"/>
    <rect x="250" y="136" width="790" height="6" fill="#8a8d91"/>
    <rect x="250" y="334" width="790" height="6" fill="#8a8d91"/>
    <polygon points="900,480 1040,360 1040,400 950,480" fill="#f35a1c"/>
    <circle cx="190" cy="240" r="140" fill="#8a8d91"/>
  </svg>
  <div class="side-copy">
    <p class="services">INSULATION • FOUNDATION REPAIR • WATERPROOFING</p>
    <h1 class="brand-name">BRIGHTNEST</h1>
    <p class="brand-sub">SEAL AND FOOTING</p>
    <p class="slogan">Snug Walls, Steady Halls</p>
    <p class="phone"><svg width="30" height="30" viewBox="0 0 30 30"><circle cx="15" cy="15" r="13" fill="none" stroke="#fff" stroke-width="2.5"/><path d="M10 8.5l3 0 1 4-2 1.3a9 9 0 0 0 4.2 4.2l1.3-2 4 1 0 3a2 2 0 0 1-2 2A12 12 0 0 1 8 10.5a2 2 0 0 1 2-2z" fill="#fff"/></svg>(555) 271-6384</p>
    <p class="web-pill">WWW.BRIGHTNEST-CREW.EXAMPLE</p>
  </div>
</section>

<!-- Curb-side panel -->
<section class="panel side side--curb">
  <svg class="panel-art" viewBox="0 0 1040 480" preserveAspectRatio="none" aria-hidden="true">
    <defs>
      <linearGradient id="sideOrange2" x1="1" y1="0" x2="0" y2="1">
        <stop offset="0" stop-color="#f04a14"/><stop offset=".6" stop-color="#e8390e"/><stop offset="1" stop-color="#d42a0a"/>
      </linearGradient>
    </defs>
    <rect width="1040" height="480" fill="url(#sideOrange2)"/>
    <polygon points="0,0 300,0 250,140 250,340 300,480 0,480" fill="#0d0d0d"/>
    <polygon points="300,0 325,0 275,140 250,140" fill="#ffffff"/>
    <polygon points="250,340 275,340 325,480 300,480" fill="#ffffff"/>
    <rect x="250" y="140" width="790" height="196" fill="#efefef"/>
    <rect x="250" y="136" width="790" height="6" fill="#8a8d91"/>
    <rect x="250" y="334" width="790" height="6" fill="#8a8d91"/>
    <polygon points="900,480 1040,360 1040,400 950,480" fill="#f35a1c"/>
    <circle cx="190" cy="240" r="140" fill="#8a8d91"/>
  </svg>
  <div class="side-copy">
    <p class="services">INSULATION • FOUNDATION REPAIR • WATERPROOFING</p>
    <h2 class="brand-name">BRIGHTNEST</h2>
    <p class="brand-sub">SEAL AND FOOTING</p>
    <p class="slogan">Snug Walls, Steady Halls</p>
    <p class="phone"><svg width="30" height="30" viewBox="0 0 30 30"><circle cx="15" cy="15" r="13" fill="none" stroke="#fff" stroke-width="2.5"/><path d="M10 8.5l3 0 1 4-2 1.3a9 9 0 0 0 4.2 4.2l1.3-2 4 1 0 3a2 2 0 0 1-2 2A12 12 0 0 1 8 10.5a2 2 0 0 1 2-2z" fill="#fff"/></svg>(555) 271-6384</p>
    <p class="web-pill">WWW.BRIGHTNEST-CREW.EXAMPLE</p>
  </div>
</section>

<!-- Rear door, orange option -->
<section class="panel rear rear--orange">
  <svg class="panel-art" viewBox="0 0 440 430" preserveAspectRatio="none" aria-hidden="true">
    <defs>
      <radialGradient id="rearOrange" cx=".5" cy=".2" r=".8">
        <stop offset="0" stop-color="#f35a1c"/><stop offset="1" stop-color="#d42a0a"/>
      </radialGradient>
    </defs>
    <rect width="440" height="430" fill="url(#rearOrange)"/>
    <rect y="162" width="440" height="140" fill="#efefef"/>
    <rect y="158" width="440" height="5" fill="#8a8d91"/>
    <rect y="300" width="440" height="5" fill="#8a8d91"/>
    <polygon points="0,375 45,345 120,400 120,430 0,430" fill="#f35a1c"/>
    <circle cx="220" cy="85" r="66" fill="#8a8d91"/>
  </svg>
  <div class="side-copy" style="left:0;width:440px;height:430px">
    <h2 class="brand-name">BRIGHTNEST</h2>
    <p class="brand-sub">SEAL AND FOOTING</p>
    <p class="slogan">Snug Walls, Steady Halls</p>
    <p class="services">INSULATION • FOUNDATION REPAIR • WATERPROOFING</p>
    <p class="phone"><svg width="22" height="22" viewBox="0 0 30 30"><circle cx="15" cy="15" r="13" fill="none" stroke="#fff" stroke-width="2.5"/><path d="M10 8.5l3 0 1 4-2 1.3a9 9 0 0 0 4.2 4.2l1.3-2 4 1 0 3a2 2 0 0 1-2 2A12 12 0 0 1 8 10.5a2 2 0 0 1 2-2z" fill="#fff"/></svg>(555) 271-6384</p>
    <p class="web-pill">WWW.BRIGHTNEST-CREW.EXAMPLE</p>
  </div>
</section>

<!-- Rear door, black option -->
<section class="panel rear rear--black">
  <svg class="panel-art" viewBox="0 0 440 430" preserveAspectRatio="none" aria-hidden="true">
    <defs>
      <radialGradient id="rearBlack" cx=".5" cy=".2" r=".8">
        <stop offset="0" stop-color="#2a2a2a"/><stop offset="1" stop-color="#0d0d0d"/>
      </radialGradient>
    </defs>
    <rect width="440" height="430" fill="url(#rearBlack)"/>
    <rect y="162" width="440" height="140" fill="#efefef"/>
    <rect y="158" width="440" height="5" fill="#8a8d91"/>
    <rect y="300" width="440" height="5" fill="#8a8d91"/>
    <polygon points="0,375 45,345 120,400 120,430 0,430" fill="#2a2a2a"/>
    <circle cx="220" cy="85" r="66" fill="#8a8d91"/>
  </svg>
  <div class="side-copy" style="left:0;width:440px;height:430px">
    <h2 class="brand-name">BRIGHTNEST</h2>
    <p class="brand-sub">SEAL AND FOOTING</p>
    <p class="slogan">Snug Walls, Steady Halls</p>
    <p class="services">INSULATION • FOUNDATION REPAIR • WATERPROOFING</p>
    <p class="phone"><svg width="22" height="22" viewBox="0 0 30 30"><circle cx="15" cy="15" r="13" fill="none" stroke="#fff" stroke-width="2.5"/><path d="M10 8.5l3 0 1 4-2 1.3a9 9 0 0 0 4.2 4.2l1.3-2 4 1 0 3a2 2 0 0 1-2 2A12 12 0 0 1 8 10.5a2 2 0 0 1 2-2z" fill="#fff"/></svg>(555) 271-6384</p>
    <p class="web-pill">WWW.BRIGHTNEST-CREW.EXAMPLE</p>
  </div>
</section>

</body>
</html>
```